Web App Design Project

Need to provide graphical design of 2 web pages according to attached wireframes.

Colors should be adjusted for the 65+ population meaning not too bright.

App logo should be created as well - logo should represent long and good life.

Target Market(s)

65 years old and above

```html
<!DOCTYPE html>
<html lang="en">
<head>
<meta charset="utf-8">
<title>Medications – Daily Schedule</title>
<link rel="stylesheet" href="https://fonts.googleapis.com/css2?family=Arimo:wght@400;700&display=swap">
<style>
:root{
  --page-bg:#d9dcd6;
  --header-top:#86b57f;
  --header-bottom:#4e8a4d;
  --header-line:#3f7340;
  --green:#4d8f4b;
  --green-text:#4a8b48;
  --panel:#f3f3f3;
  --white:#ffffff;
  --divider:#e0e0e0;
  --slate:#5f6478;
  --slate-light:#8e92a0;
  --card-border:#b9bccb;
  --nav-bg:#3c4054;
  --nav-active:#4d5166;
  --nav-divider:#34384a;
  --nav-text:#c3c6d2;
  --text:#5a5e6e;
}
*{box-sizing:border-box;margin:0;padding:0}
html,body{width:1200px;height:900px;overflow:hidden}
body{background:var(--page-bg);font-family:"Arimo",Arial,sans-serif;position:relative}
.app{position:absolute;left:100px;top:120px;width:1000px;height:660px;background:var(--white);box-shadow:0 10px 40px rgba(0,0,0,.25)}
.abs{position:absolute}

/* header */
.topbar{left:0;top:0;width:1000px;height:60px;background:linear-gradient(var(--header-top),var(--header-bottom));border-bottom:1px solid var(--header-line);color:var(--white)}
.brand{left:0;top:0;width:200px;height:60px;border-right:1px solid rgba(255,255,255,.2);display:flex;align-items:center;padding-left:20px;gap:12px}
.brand-dot{width:34px;height:34px;border-radius:50%;background:rgba(255,255,255,.85)}
.brand-name{font-weight:700;font-size:18px;line-height:18px}
.brand-slogan{font-weight:700;font-size:9px;margin-top:2px}
.welcome{left:215px;top:21px;font-size:16px;color:#eef5ec}
.welcome b{color:var(--white)}
.text-size{left:611px;top:18px;display:flex;align-items:baseline;gap:10px;color:var(--white)}
.search{left:686px;top:15px;width:163px;height:30px;border:1px solid rgba(255,255,255,.35);background:rgba(255,255,255,.12);font-size:14px;color:#d8e8d5;padding:7px 9px}
.search svg{position:absolute;right:8px;top:7px}
.btn-head{top:15px;height:30px;background:#55904f;border:1px solid #3e733d;box-shadow:inset 0 1px 0 rgba(255,255,255,.25);font-weight:700;font-size:16px;color:var(--white);text-align:center;line-height:28px;border-radius:2px}

/* sub header */
.subbar{left:0;top:60px;width:1000px;height:70px;background:var(--panel);border-bottom:1px solid var(--divider)}
.section-title{left:0;top:84px;width:200px;text-align:center;font-weight:700;font-size:17px;color:var(--green-text)}
.sub-divider{left:199px;top:60px;width:1px;height:70px;background:var(--divider)}
.add-med{left:230px;top:82px;display:flex;align-items:center;gap:7px;font-weight:700;font-size:16px;color:var(--green-text)}
.settings{left:944px;top:82px}

/* sidebar */
.sidebar{left:0;top:130px;width:200px;height:400px;background:var(--panel);border-right:1px solid var(--divider)}
.period{position:absolute;left:10px;width:190px;height:90px;display:flex;align-items:center;padding-left:30px;gap:10px;font-weight:700;font-size:16px;color:var(--slate)}
.period.active{background:var(--white);box-shadow:0 2px 3px rgba(0,0,0,.08);width:191px}

/* cards */
.med{left:230px;width:741px;height:61px;border:1px solid var(--card-border);border-radius:3px;background:var(--white)}
.med.done{border-color:#9fd096}
.med-btn{position:absolute;left:14px;top:15px;width:100px;height:30px;border-radius:2px;background:var(--slate-light);color:var(--white);font-weight:700;font-size:13px;line-height:30px;text-align:center}
.med-btn.taken{background:var(--green)}
.med-name{position:absolute;left:147px;top:21px;font-size:16px;color:var(--text)}
.med-dose{position:absolute;left:576px;top:21px;font-weight:700;font-size:16px;color:var(--text)}
.med.done .med-dose{color:var(--green-text)}
.med-form{position:absolute;left:610px;top:17px}
.med-info{position:absolute;left:700px;top:20px}

/* bottom nav */
.nav{left:0;top:530px;width:1000px;height:130px;background:var(--nav-bg);display:flex}
.nav-item{width:143px;height:130px;border-right:1px solid var(--nav-divider);position:relative;color:var(--nav-text);font-weight:700;font-size:14px;text-align:center;line-height:17px}
.nav-item:last-child{border-right:0}
.nav-item.active{background:var(--nav-active);color:var(--white)}
.nav-item svg{position:absolute;left:50%;top:30px;transform:translateX(-50%)}
.nav-label{position:absolute;left:0;right:0;top:82px}
.nav-label.two{top:74px}
</style>
</head>
<body>
<main class="app">
  <header class="abs topbar">
    <div class="abs brand">
      <span class="brand-dot"></span>
      <div><div class="brand-name">AppName</div><div class="brand-slogan">Here is your slogan</div></div>
    </div>
    <div class="abs welcome">Welcome back, <b>Walter Grant</b></div>
    <div class="abs text-size"><span style="font-size:11px">A</span><b style="font-size:17px">A</b><span style="font-size:20px;opacity:.8">A</span></div>
    <div class="abs search">Search
      <svg width="16" height="16" viewBox="0 0 16 16"><circle cx="6.5" cy="6.5" r="5" fill="none" stroke="#e4eee2" stroke-width="2"/><path d="M10 10l5 5" stroke="#e4eee2" stroke-width="2.4"/></svg>
    </div>
    <div class="abs btn-head" style="left:888px;width:32px">?</div>
    <div class="abs btn-head" style="left:934px;width:52px">Exit</div>
  </header>

  <div class="abs subbar"></div>
  <div class="abs sub-divider"></div>
  <div class="abs section-title">Medications</div>
  <div class="abs add-med">
    <svg width="26" height="26" viewBox="0 0 26 26"><circle cx="13" cy="13" r="11.5" fill="none" stroke="#4a8b48" stroke-width="2"/><path d="M13 7v12M7 13h12" stroke="#4a8b48" stroke-width="3"/></svg>
    Add medication
  </div>
  <svg class="abs settings" width="26" height="26" viewBox="0 0 26 26"><circle cx="13" cy="13" r="11.5" fill="none" stroke="#5f6478" stroke-width="2"/><circle cx="13" cy="13" r="5" fill="none" stroke="#5f6478" stroke-width="3" stroke-dasharray="3 1.5"/><circle cx="13" cy="13" r="2" fill="#5f6478"/></svg>

  <nav class="abs sidebar">
    <div class="period active" style="top:0">
      <svg width="32" height="32" viewBox="0 0 32 32" fill="none" stroke="#5f6478" stroke-width="2"><path d="M9 15a7 7 0 0 1 14 0M16 3v4M6 7l3 3M26 7l-3 3M2 15h4M26 15h4M2 19h28M2 24h28M2 29h28"/></svg>Morning</div>
    <div class="period" style="top:100px">
      <svg width="32" height="32" viewBox="0 0 32 32" fill="none" stroke="#5f6478" stroke-width="2"><circle cx="16" cy="16" r="7"/><path d="M16 2v4M16 26v4M2 16h4M26 16h4M6 6l3 3M23 23l3 3M26 6l-3 3M9 23l-3 3"/></svg>Noon</div>
    <div class="period" style="top:200px">
      <svg width="32" height="32" viewBox="0 0 32 32" fill="none" stroke="#5f6478" stroke-width="2"><path d="M9 14a6 6 0 0 1 12-1M15 3v3M5 7l2 2M25 7l-2 2"/><path d="M7 29a5 5 0 0 1 0-10 7 7 0 0 1 13-1 5.5 5.5 0 0 1 5 11z"/></svg>Afternoon</div>
    <div class="period" style="top:300px">
      <svg width="32" height="32" viewBox="0 0 32 32" fill="none" stroke="#5f6478" stroke-width="2"><path d="M18 3a13 13 0 1 0 12 18A11 11 0 0 1 18 3z"/></svg>Night</div>
  </nav>

  <section class="abs med done" style="top:160px">
    <div class="med-btn taken">✓&nbsp; Taken</div>
    <div class="med-name">Relvane (indomethacin)</div>
    <div class="med-dose">4x</div>
    <svg class="med-form" width="24" height="24" viewBox="0 0 24 24"><rect x="2" y="8" width="20" height="8" rx="4" transform="rotate(-45 12 12)" fill="none" stroke="#6a6e7e" stroke-width="1.8"/><path d="M12 12l5-5a3.5 3.5 0 0 1 5 5l-5 5z" fill="#6a6e7e"/></svg>
    <svg class="med-info" width="20" height="20" viewBox="0 0 20 20"><circle cx="10" cy="10" r="9" fill="none" stroke="#a8abb8"/><text x="10" y="15" text-anchor="middle" font-size="12" font-style="italic" fill="#a8abb8" font-family="Georgia,serif">i</text></svg>
  </section>

  <section class="abs med" style="top:252px">
    <div class="med-btn">Mark as taken</div>
    <div class="med-name">Dabrixa (dabigatran)</div>
    <div class="med-dose">2x</div>
    <svg class="med-form" width="24" height="24" viewBox="0 0 24 24" fill="none" stroke="#6a6e7e" stroke-width="1.6"><rect x="2" y="6" width="12" height="16" rx="2"/><path d="M3 3h10v3H3zM5 12h6v5H5z"/><ellipse cx="19" cy="6" rx="2.5" ry="3.5"/><path d="M19 10v12"/></svg>
    <svg class="med-info" width="20" height="20" viewBox="0 0 20 20"><circle cx="10" cy="10" r="9" fill="none" stroke="#a8abb8"/><text x="10" y="15" text-anchor="middle" font-size="12" font-style="italic" fill="#a8abb8" font-family="Georgia,serif">i</text></svg>
  </section>

  <section class="abs med" style="top:344px">
    <div class="med-btn">Mark as taken</div>
    <div class="med-name">Omerel (omeprazole)</div>
    <div class="med-dose">1x</div>
    <svg class="med-form" width="24" height="24" viewBox="0 0 24 24" fill="none" stroke="#6a6e7e" stroke-width="1.6"><path d="M16 2l6 6M19 5l-4 4M14 6l4 4L8 20H4v-4z M6 14l2 2M9 11l2 2M2 22l2-2"/></svg>
    <svg class="med-info" width="20" height="20" viewBox="0 0 20 20"><circle cx="10" cy="10" r="9" fill="none" stroke="#a8abb8"/><text x="10" y="15" text-anchor="middle" font-size="12" font-style="italic" fill="#a8abb8" font-family="Georgia,serif">i</text></svg>
  </section>

  <nav class="abs nav">
    <div class="nav-item active">
      <svg width="32" height="34" viewBox="0 0 32 34"><rect x="4" y="2" width="10" height="22" rx="5" transform="rotate(-25 9 13)" fill="none" stroke="#fff" stroke-width="2"/><rect x="12" y="10" width="11" height="22" rx="5.5" transform="rotate(-40 17 21)" fill="#fff"/></svg>
      <div class="nav-label">Medications</div></div>
    <div class="nav-item">
      <svg width="32" height="34" viewBox="0 0 32 34" fill="none" stroke="#c3c6d2" stroke-width="2"><path d="M24 2a4 4 0 0 1 5 5L13 23l-5-5z"/><path d="M8 18l-4 4v3h3l4-4M2 32l3-3M17 10l2 2M14 13l2 2M20 7l2 2"/></svg>
      <div class="nav-label two">Home<br>Measurements</div></div>
    <div class="nav-item">
      <svg width="32" height="34" viewBox="0 0 32 34"><rect x="2" y="5" width="28" height="26" fill="none" stroke="#c3c6d2" stroke-width="2"/><rect x="2" y="5" width="28" height="6" fill="#c3c6d2"/><path d="M9 2v6M23 2v6" stroke="#c3c6d2" stroke-width="2.5"/><text x="16" y="27" text-anchor="middle" font-size="12" font-family="Arimo,Arial,sans-serif" fill="#c3c6d2">17</text></svg>
      <div class="nav-label">My Schedule</div></div>
    <div class="nav-item">
      <svg width="34" height="34" viewBox="0 0 34 34" fill="none" stroke="#c3c6d2" stroke-width="2"><rect x="2" y="2" width="30" height="22"/><path d="M5 15h7l3-6 4 10 3-6h7M12 24l-5 9M22 24l5 9"/></svg>
      <div class="nav-label">Lab Test Results</div></div>
    <div class="nav-item">
      <svg width="34" height="34" viewBox="0 0 34 34" fill="none" stroke="#c3c6d2" stroke-width="2"><rect x="2" y="2" width="6" height="6"/><rect x="2" y="14" width="6" height="6"/><rect x="2" y="26" width="6" height="6"/><path d="M13 5h19M13 17h19M13 29h19" stroke-width="3"/></svg>
      <div class="nav-label two">Checkups &amp;<br>Procedures</div></div>
    <div class="nav-item">
      <svg width="34" height="34" viewBox="0 0 34 34" fill="#c3c6d2"><ellipse cx="17" cy="10" rx="7" ry="9"/><path d="M2 33c0-8 6-12 15-12s15 4 15 12z"/></svg>
      <div class="nav-label">My Profile</div></div>
    <div class="nav-item">
      <svg width="34" height="34" viewBox="0 0 34 34" fill="#c3c6d2"><path d="M17 31L4 17a8 8 0 0 1 13-11 8 8 0 0 1 13 11z"/></svg>
      <div class="nav-label two">My Health Care<br>Providers</div></div>
  </nav>
</main>
</body>
</html>
```